Hollow Marigold Distillery

I need a label designed for my small distillery. I’d like it to have a rose, and the name hollow marigold in script writing. I need the graphic to fit a standard gin bottle and I’ll need to be able to edit it depending on alcohol, warning and descriptions. I want it to look elegant and attractive, but slightly daring too. It’s a 700ml oslo bottle
Target Market(s)
Bespoke gin and vodka drinkers
Industry/Entity Type
Beverage
Font styles to use
Script
Other font styles liked:
- Something easy to read
Requirements
Must have
- Room for me to add and remove text depending on the drink
Nice to have
- Hollow marigold in script, slight colour on the rose and black writing

```html
<!DOCTYPE html>
<html lang="en">
<head>
<meta charset="utf-8">
<title>Hollow Marigold – Rose Gin Labels</title>
<link rel="stylesheet" href="https://fonts.googleapis.com/css2?family=Great+Vibes&family=Yellowtail&family=Crimson+Text&family=Oswald:wght@500&display=swap">
<style>
  :root {
    --paper: #ffffff;
    --ink: #111111;
    --title-shadow: #c9c9c9;
    --rose-light: #f5c6bd;
    --rose-mid: #d98b84;
    --rose-deep: #a2463e;
    --rose-soft: #fbe3dc;
    --blush: #f7d2c8;
  }
  * { margin: 0; padding: 0; box-sizing: border-box; }
  html, body {
    width: 1200px; height: 665px; overflow: hidden;
    background: var(--paper);
  }
  .sheet { position: relative; width: 1200px; height: 665px; }

  .label {
    position: absolute; top: 18px; width: 568px; height: 630px;
    background: var(--paper);
    box-shadow: 1px 2px 4px rgba(0,0,0,0.28);
    overflow: hidden;
  }
  .label--classic { left: 20px; }
  .label--bold { left: 609px; }

  .label__frame {
    position: absolute; left: 19px; top: 21px; width: 532px; height: 589px;
    border: 4px solid;
    border-image: linear-gradient(90deg, var(--rose-light), var(--rose-deep) 30%, var(--rose-mid) 55%, var(--rose-light) 80%, var(--rose-mid)) 1;
  }
  .label--bold .label__frame {
    border-image: linear-gradient(90deg, var(--rose-light), var(--rose-mid) 30%, var(--rose-light) 60%, var(--rose-soft) 80%, var(--rose-mid)) 1;
  }

  .label__wash {
    position: absolute; left: 23px; top: 25px; width: 240px; height: 581px;
    background:
      radial-gradient(ellipse 90px 70px at 60px 80px, rgba(244,176,160,0.55), transparent 75%),
      radial-gradient(ellipse 110px 90px at 100px 390px, rgba(244,180,165,0.45), transparent 75%),
      linear-gradient(90deg, rgba(247,210,200,0.75), rgba(247,210,200,0.35) 70%, rgba(247,210,200,0) 100%);
  }

  .label__title {
    position: absolute; left: 0; width: 100%; text-align: center;
    color: var(--ink); line-height: 1; white-space: nowrap;
    text-shadow: 3px 3px 0 var(--title-shadow);
  }
  .label--classic .label__title { font-family: "Great Vibes", cursive; }
  .label--classic .title-line--one { top: 70px; font-size: 86px; left: -4px; }
  .label--classic .title-line--two { top: 160px; font-size: 98px; left: 10px; }
  .label--bold .label__title { font-family: "Yellowtail", cursive; }
  .label--bold .title-line--one { top: 78px; font-size: 94px; left: 4px; }
  .label--bold .title-line--two { top: 172px; font-size: 100px; left: 2px; }

  .label__rose {
    position: absolute; top: 288px; width: 386px; height: 170px;
    border-radius: 50% 50% 45% 45% / 55% 55% 45% 45%;
    background: radial-gradient(ellipse at 65% 45%, rgba(217,139,132,0.55), rgba(245,198,189,0.35) 60%, rgba(255,255,255,0) 100%);
  }
  .label--classic .label__rose { left: 89px; }
  .label--bold .label__rose { left: 88px; }

  .label__band {
    position: absolute; left: 23px; top: 495px; width: 524px; height: 53px;
    background: linear-gradient(90deg, #c97570, var(--rose-deep) 35%, #c97a78 55%, #c66f6c 72%, #db9590);
    color: var(--paper); font-family: "Crimson Text", serif; font-size: 31px;
    display: flex; align-items: center; justify-content: center; letter-spacing: 0.5px;
  }
  .label__pill {
    position: absolute; left: 274px; top: 487px; width: 273px; height: 53px;
    border-radius: 27px 0 0 27px;
    background: linear-gradient(90deg, var(--blush), var(--rose-soft) 50%, var(--rose-light));
    color: var(--ink); font-family: "Crimson Text", serif; font-size: 31px;
    display: flex; align-items: center; justify-content: center; letter-spacing: 0.5px;
  }

  .label__details {
    position: absolute; font-family: "Oswald", sans-serif; font-weight: 500;
    font-size: 22px; color: var(--ink); white-space: nowrap; letter-spacing: -0.3px;
    transform: scaleX(0.88);
  }
  .label--classic .label__details { left: 0; width: 100%; text-align: center; top: 561px; transform-origin: 285px 0; }
  .label--bold .label__details { left: 274px; width: 273px; text-align: center; top: 553px; }
</style>
</head>
<body>
<main class="sheet">
  <section class="label label--classic">
    <div class="label__wash" role="img" aria-label="Soft blush watercolour wash"></div>
    <div class="label__frame"></div>
    <h1 class="label__title title-line--one">Hollow</h1>
    <p class="label__title title-line--two">Marigold</p>
    <div class="label__rose" role="img" aria-label="Rose-gold line illustration of roses and blossoms"></div>
    <div class="label__band">ROSE GIN</div>
    <p class="label__details">40% ABV&nbsp;&nbsp;|&nbsp;&nbsp;700 ML</p>
  </section>

  <section class="label label--bold">
    <div class="label__frame"></div>
    <h2 class="label__title title-line--one">Hollow</h2>
    <p class="label__title title-line--two">Marigold</p>
    <div class="label__rose" role="img" aria-label="Rose-gold line illustration of roses and blossoms"></div>
    <div class="label__pill">ROSE GIN</div>
    <p class="label__details">40% ABV&nbsp;&nbsp;|&nbsp;&nbsp;700 ML</p>
  </section>
</main>
</body>
</html>
```